Birchwell Agency Condominium mail merge

We need a marketing proposal letter design to do a mail merge to potential e customers. We included our logo and an example of my miserable attempt to create a template. We are looking for a modern and attractive proposal template. Here is our website https://www.birchwellagency.example to be used for any additional information needed about us and our services.

Target Market(s)

New prospects

Industry/Entity Type

Insurance Agency

Requirements
Must have
• My project must have a modern professional look with merge fields similar to the file uploaded with this project.
Nice to have
• it would like have a condominium and a car icon graphic depicting there is additional discounts for both quotes bundled.
Should not have
• My project should not have any other logos or company name

```html
<!DOCTYPE html>
<html lang="en">
<head>
<meta charset="utf-8">
<title>Birchwell Agency – Letterhead</title>
<link href="https://fonts.googleapis.com/css2?family=PT+Sans:wght@400;700&family=Open+Sans:wght@700&display=swap" rel="stylesheet">
<style>
  :root {
    --brand-green: #3cb54a;
    --brand-orange: #f47b20;
    --text: #4a4a4a;
    --heading: #555555;
    --paper: #ffffff;
  }
  * { box-sizing: border-box; margin: 0; padding: 0; }
  html, body { width: 1059px; height: 1200px; overflow: hidden; background: var(--paper); }
  .letter {
    position: relative;
    width: 1059px;
    height: 1200px;
    background: var(--paper);
    font-family: "PT Sans", sans-serif;
    color: var(--text);
  }
  .brand {
    position: absolute;
    left: 80px;
    top: 62px;
    display: flex;
    align-items: center;
    gap: 12px;
    font-family: "PT Sans", sans-serif;
    font-weight: 700;
    font-size: 34px;
    color: var(--brand-green);
  }
  .brand-dot {
    width: 22px; height: 22px;
    border-radius: 50%;
    background: var(--brand-orange);
  }
  .salutation {
    position: absolute;
    left: 80px;
    top: 276px;
    font-family: "Open Sans", Arial, sans-serif;
    font-weight: 700;
    font-size: 18px;
    color: var(--heading);
  }
  .body {
    position: absolute;
    left: 80px;
    top: 322px;
    width: 899px;
  }
  .body p {
    font-size: 17px;
    line-height: 22px;
    text-align: justify;
    margin-bottom: 22px;
  }
  .signature {
    position: absolute;
    left: 80px;
    top: 918px;
    width: 158px;
    height: 78px;
    background: linear-gradient(180deg, #f4f4f4, #e6e6e6);
    border-radius: 4px;
  }
  .footer-bar {
    position: absolute;
    left: 60px;
    top: 1125px;
    width: 14px;
    height: 75px;
    background: var(--brand-green);
  }
  .footer-info {
    position: absolute;
    left: 84px;
    top: 1128px;
    font-size: 11.5px;
    line-height: 17px;
    color: var(--text);
  }
  .footer-info .company { color: var(--brand-green); font-weight: 700; }
  .footer-info .label { color: var(--brand-green); font-weight: 700; }
  .footer-rule {
    position: absolute;
    left: 74px;
    top: 1181px;
    width: 860px;
    height: 1px;
    background: var(--brand-green);
  }
  .web-tag {
    position: absolute;
    right: 64px;
    top: 1172px;
    height: 20px;
    padding: 0 14px;
    background: var(--brand-orange);
    color: #fff;
    font-size: 12px;
    line-height: 20px;
    letter-spacing: 0.5px;
    clip-path: polygon(8px 0, calc(100% - 8px) 0, 100% 50%, calc(100% - 8px) 100%, 8px 100%, 0 50%);
  }
  .web-tag strong { font-weight: 700; }
</style>
</head>
<body>
<main class="letter">
  <header class="brand">
    <span class="brand-dot"></span>
    <span class="brand-name">Birchwell Agency</span>
  </header>

  <h1 class="salutation">Dear Mr. Carter,</h1>

  <section class="body">
    <p>Lorem Ipsum is simply dummy text of the printing and typesetting industry. Lorem Ipsum has been the industry's standard dummy text ever since the 1500s, when an unknown printer took a galley of type and scrambled it to make a type specimen book. It has survived not only five centuries, but also the leap into electronic typesetting, remaining essentially unchanged.</p>
    <p>The standard chunk of Lorem Ipsum used since the 1500s is reproduced below for those interested. Sections 1.10.32 and 1.10.33 from "de Finibus Bonorum et Malorum" by Marcus Quell are also reproduced in their exact original form, accompanied by English versions from the 1914 translation by H. Penwright</p>
    <p>Lorem Ipsum is simply dummy text of the printing and typesetting industry. Lorem Ipsum has been the industry's standard dummy text ever since the 1500s, when an unknown printer took a galley of type and scrambled it to make a type specimen book. It has survived not only five centuries, but also the leap into electronic typesetting, remaining essentially unchanged. It was popularised in the</p>
    <p>Lorem Ipsum is simply dummy text of the printing and typesetting industry. Lorem Ipsum has been the industry's standard dummy text ever since the 1500s, when an unknown printer took a galley of type and scrambled it to make a type specimen book. It has survived not only five centuries, but also the leap into electronic typesetting, remaining essentially unchanged. It was popularised in the</p>
    <p>Lorem Ipsum is simply dummy text of the printing and typesetting industry. Lorem Ipsum has been the industry's standard dummy text ever since the 1500s, when an unknown printer took a galley of type and scrambled it to make a type specimen book.</p>
  </section>

  <div class="signature" role="img" aria-label="Handwritten signature of the sender"></div>

  <footer>
    <div class="footer-bar"></div>
    <div class="footer-info">
      <div class="company">Birchwell Agency, Inc</div>
      <div>2450 Lakeview Parkway Ste. 210 Maplebrook, FL 32801</div>
      <div><span class="label">P.</span> 555-014-2290 &nbsp;<span class="label">E.</span> hello@birchwellagency.example</div>
    </div>
    <div class="footer-rule"></div>
    <div class="web-tag">www.<strong>birchwellagency</strong>.example</div>
  </footer>
</main>
</body>
</html>
```